BOLD & MINIMALIST DESIGN NEEDED

We want a very bold but minimalistic business card design that is impactful and utilizes both sides of the business card. Our current logo is included for your use.

We want bold fonts and good use of negative space. We don't want the logo to overpower the design.

Target Market(s)

Professionals who are building new commercial buildings.

Industry/Entity Type

Construction

Contact Information for Business Card

Name, Title, email, office phone, cell phone, website

Font styles to use
Serif
Sans Serif

Requirements
Must have
• Bold design!

```html
<!DOCTYPE html>
<html lang="en">
<head>
<meta charset="utf-8">
<title>Ridgecrest Business Card</title>
<link href="https://fonts.googleapis.com/css2?family=Arimo:wght@400;700&display=swap" rel="stylesheet">
<style>
  :root {
    --canvas: #e6e6e6;
    --green: #86c232;
    --green-light: #bde08e;
    --ink: #111111;
    --white: #ffffff;
  }
  * { margin: 0; padding: 0; box-sizing: border-box; }
  html, body {
    width: 1200px; height: 1200px; overflow: hidden;
    background: var(--canvas);
    font-family: "Arimo", Arial, sans-serif;
  }
  .card {
    position: absolute;
    left: 256px;
    width: 688px;
    height: 393px;
    box-shadow: 0 22px 30px rgba(0,0,0,0.28);
  }
  .card--front {
    top: 159px;
    background: radial-gradient(ellipse 55% 70% at 58% 48%, var(--green-light) 0%, var(--green) 100%);
    color: var(--white);
  }
  .card--back {
    top: 653px;
    background: var(--white);
  }
  .brand {
    display: flex; align-items: center; gap: 12px;
    font-weight: 700; letter-spacing: 0.5px;
  }
  .brand__mark { display: block; }
  .card--front .brand {
    position: absolute; left: 43px; top: 62px;
    font-size: 44px; color: var(--white);
  }
  .card--front .brand__mark { width: 22px; height: 22px; background: var(--white); }
  .card--back .brand {
    position: absolute; left: 0; right: 0; top: 160px;
    justify-content: center;
    font-size: 58px; color: var(--ink);
  }
  .card--back .brand__mark { width: 30px; height: 30px; background: var(--green); }
  .person { position: absolute; left: 43px; top: 184px; }
  .person__name { font-size: 28px; font-weight: 700; color: var(--ink); letter-spacing: 0.3px; }
  .person__title { font-size: 16px; font-weight: 400; color: var(--white); margin-top: 4px; }
  .contact {
    position: absolute; left: 43px; top: 266px;
    list-style: none;
    font-size: 16.5px; line-height: 20.5px; color: var(--white);
  }
  .contact li { display: flex; align-items: center; gap: 12px; }
  .contact svg { width: 14px; height: 14px; fill: var(--ink); flex: none; }
</style>
</head>
<body>
  <section class="card card--front">
    <div class="brand"><span class="brand__mark"></span>RIDGECREST</div>
    <div class="person">
      <div class="person__name">DANIEL HART</div>
      <div class="person__title">President</div>
    </div>
    <ul class="contact">
      <li>
        <svg viewBox="0 0 16 16" aria-hidden="true"><path d="M3.6 1.2l2.3 2.6-1.2 2.1c.9 2 2.4 3.6 4.4 4.5l2.1-1.2 2.6 2.3-1.4 2.6C6.9 14 2 9.1 1 3z"/></svg>
        415-555-0182
      </li>
      <li>
        <svg viewBox="0 0 16 16" aria-hidden="true"><path d="M4 0h8v16H4zM5.5 2v10h5V2zM7 13.2h2v1.4H7z" fill-rule="evenodd"/></svg>
        415-555-0147
      </li>
      <li>
        <svg viewBox="0 0 16 16" aria-hidden="true"><path d="M1 3h14v10H1zm1.6 1.5L8 9l5.4-4.5V11.5H2.6z" fill-rule="evenodd"/></svg>
        info@ridgecrestbuild.com
      </li>
      <li>
        <svg viewBox="0 0 16 16" aria-hidden="true"><circle cx="8" cy="8" r="7"/><path d="M5 4c1 1 2 1 2 3s-2 1-2 3M10 3c0 2 2 2 2 4M9 12c1-1 2-1 3-1" stroke="#86c232" stroke-width="1.3" fill="none"/></svg>
        www.ridgecrestbuild.com
      </li>
    </ul>
  </section>

  <section class="card card--back">
    <div class="brand"><span class="brand__mark"></span>RIDGECREST</div>
  </section>
</body>
</html>
```